Web-site design for company trading in chemicals & lubricants

We need a standard 5 page web-site designed for our company based in Dubai, UAE.
The web-site should highlight our capacity to store material as well as distribute the same. The products we sell are basic chemicals - packed in bags as well as drums. Bags are big bags - 25 kgs each as well as drums - 200 litres each. We want to highlight the fact that we huge stocks of this material & can deliver by sea & road,
Please use this site as a ref - http://www.brontex-solvents.co.uk/
Besides this, we need a page dedicated to finished products that we are selling for use in the auto industry - lubricants, motor oils,brake-fluids, greases, coolants etc. This are packed in large drums as well as small cans.
It would be nice if the site could immediately also provide a ref. to our location - Dubai or that we are based in the Middle East.
We will provide our company logo for reference

```html
<!DOCTYPE html>
<html lang="en">
<head>
<meta charset="utf-8">
<title>Korvant Trading – Chemicals &amp; Lubricants</title>
<link rel="stylesheet" href="https://fonts.googleapis.com/css2?family=Open+Sans:wght@400;600&family=Philosopher:ital,wght@1,700&display=swap">
<style>
:root{
  --gold:#d3b145;
  --gold-dark:#a9861c;
  --gold-deep:#7d600e;
  --gold-text:#b8941c;
  --brown:#5b321a;
  --ink:#1f1f1f;
  --paper:#ffffff;
  --mist:#e7e7e7;
  --night:#0b0b0b;
}
*{box-sizing:border-box;margin:0;padding:0}
html,body{width:855px;height:1200px;overflow:hidden}
body{position:relative;background:var(--gold);font-family:"Open Sans",Arial,sans-serif;color:var(--ink)}
.abs{position:absolute}
.site-header{left:0;top:0;width:855px;height:147px;background:#f7f5f3}
.skyline{left:0;top:18px;width:855px;height:129px;background:linear-gradient(180deg,rgba(91,50,26,0) 0%,rgba(91,50,26,.55) 30%,var(--brown) 70%)}
.brand{left:622px;top:30px;display:flex;align-items:center;gap:8px}
.brand-dot{width:26px;height:26px;border-radius:50%;background:var(--gold-dark)}
.brand-name{font-size:25px;font-weight:600;letter-spacing:2px;color:var(--brown)}
.main-nav{left:18px;top:127px;width:820px;height:34px;background:linear-gradient(180deg,var(--gold) 0%,var(--gold-dark) 55%,var(--gold-deep) 100%);display:flex;padding-left:113px}
.main-nav a,.foot-nav a{text-decoration:none;font-size:13px}
.main-nav a{color:#fff;line-height:32px;margin-right:0}
.hero{left:18px;top:161px;width:820px;height:270px;border-radius:0 0 12px 12px;overflow:hidden;background:var(--mist)}
.hero-text{left:0;top:0;width:291px;height:270px;padding:26px 20px 0 24px;background:linear-gradient(180deg,#ececec,#dcdcdc)}
.hero-title{font-family:"Philosopher",Georgia,serif;font-style:italic;font-weight:700;font-size:25px;line-height:32px;color:#111}
.hero-copy{font-size:12.5px;line-height:26px;margin:8px 0 0 2px;color:#222}
.hero-photo{left:291px;top:0;width:529px;height:270px;background:radial-gradient(ellipse at 45% 55%,#a8651f 0%,#4a2a0e 35%,#120b05 75%)}
.hero-arrow{left:270px;top:113px;width:40px;height:40px;border-radius:50%;background:#3a2a1a;color:#fff;font-size:22px;line-height:38px;text-align:center;font-weight:600}
.content{left:18px;top:430px;width:820px;height:682px;background:var(--paper)}
.section-title{font-size:21px;color:var(--gold-text);font-weight:400}
.welcome-mark{left:11px;top:17px;width:22px;height:22px;border-radius:50%;border:3px solid var(--gold-dark)}
.welcome-title{left:38px;top:17px}
.welcome-copy{left:37px;top:57px;width:525px;font-size:11px;line-height:21px}
.btn-more{background:var(--gold);color:var(--ink);font-size:11px;padding:1px 6px;line-height:15px}
.team-photo{left:571px;top:27px;width:237px;height:130px;border-radius:6px;background:linear-gradient(135deg,#e9eef3 0%,#b9c4cf 45%,#4b5563 100%)}
.product-title{width:256px;text-align:center;font-size:20px;color:var(--gold-text)}
.product-photo{width:256px;height:123px;border-radius:8px;box-shadow:0 8px 8px -6px rgba(0,0,0,.25)}
.product-copy{width:245px;font-size:11px;line-height:20.5px}
.shade{left:0;top:400px;width:820px;height:14px;background:linear-gradient(180deg,rgba(0,0,0,.06),rgba(0,0,0,0))}
.news-item{left:18px;display:flex;gap:14px;align-items:flex-start}
.news-date{width:58px;height:58px;border-radius:50%;border:4px solid #eee;background:radial-gradient(circle at 40% 35%,#e9c44a,#b08510);color:#fff;font-size:11px;line-height:15px;text-align:center;padding-top:10px;font-weight:600;box-shadow:0 1px 3px rgba(0,0,0,.25);flex:none}
.news-text{width:165px;font-size:11px;line-height:13px;padding-top:6px}
.form-label{font-size:10px;left:311px}
.field{left:362px;width:152px;height:22px;border:1px solid #ddd;border-radius:4px;box-shadow:inset 0 -2px 2px rgba(0,0,0,.12);background:#fff}
.btn-submit{left:399px;top:618px;width:92px;height:20px;border-radius:6px;background:linear-gradient(180deg,#f1d060,#c0971a);color:#fff;font-size:12px;font-weight:600;text-align:center;line-height:20px}
.map{left:567px;top:460px;width:149px;height:99px;background:linear-gradient(135deg,#cdd9e6,#e9e4cf 55%,#d8c6a0)}
.contact-info{left:566px;font-size:11px}
.foot-nav{left:0;top:1112px;width:855px;height:46px;display:flex;padding-left:34px}
.foot-nav a{color:#3a2a10;line-height:46px}
.social{top:1125px;width:28px;height:28px;border-radius:50%;box-shadow:0 1px 3px rgba(0,0,0,.35)}
.site-footer{left:0;top:1158px;width:855px;height:42px;background:var(--night);color:var(--gold);font-size:11px;text-align:center;line-height:42px}
</style>
</head>
<body>
<header class="site-header abs">
  <div class="skyline abs" role="img" aria-label="Brown city skyline silhouette with cranes"></div>
  <div class="brand abs"><span class="brand-dot"></span><span class="brand-name">KORVANT</span></div>
</header>

<nav class="main-nav abs">
  <a href="#" style="width:92px">Home</a>
  <a href="#" style="width:115px">About Us</a>
  <a href="#" style="width:139px">Functionalities</a>
  <a href="#" style="width:107px">Products</a>
  <a href="#">Contact Us</a>
</nav>

<section class="hero abs">
  <div class="hero-text abs">
    <h1 class="hero-title">Lorem Ipsum is simply dummy text</h1>
    <p class="hero-copy">the printing and typesetting industry. Lorem Ipsum has been the industry's standard dummy text ever since the 1500s, when an unknown printer took a galley</p>
  </div>
  <div class="hero-photo abs" role="img" aria-label="Refinery plant lit up at night"></div>
  <div class="hero-arrow abs">«</div>
</section>

<main class="content abs">
  <span class="welcome-mark abs"></span>
  <h2 class="section-title welcome-title abs">Welcome To Our Website</h2>
  <p class="welcome-copy abs">There are many variations of passages of Lorem Ipsum available, but the majority have suffered alteration in some form, by injected humour, or randomised words which don't look even slightly believable. If you are going to use a passage of Lorem Ipsum, you need to be sure there isn't anything embarrassing hidden in the middle of text. All the Lorem Ipsum generators</p>
  <span class="btn-more abs" style="left:473px;top:135px">Read more...</span>
  <div class="team-photo abs" role="img" aria-label="Business team standing together"></div>

  <h3 class="product-title abs" style="left:6px;top:166px">Motor Oils</h3>
  <h3 class="product-title abs" style="left:271px;top:166px">Brake-Fluids</h3>
  <h3 class="product-title abs" style="left:546px;top:164px">Greases</h3>
  <div class="product-photo abs" style="left:15px;top:197px;background:linear-gradient(135deg,#d8d8d8,#8c8c8c 60%,#5a4020)" role="img" aria-label="Motor oil poured into an engine"></div>
  <div class="product-photo abs" style="left:283px;top:197px;background:radial-gradient(ellipse at 55% 55%,#3d4a10,#8cab25 45%,#d9e88a)" role="img" aria-label="Green fluid splash"></div>
  <div class="product-photo abs" style="left:551px;top:197px;background:radial-gradient(ellipse at 45% 50%,#bdbdbd,#4a4a4a 60%,#111)" role="img" aria-label="Hands holding machine gears"></div>
  <p class="product-copy abs" style="left:20px;top:334px">There are many variations of passages of Lorem Ipsum available, but the majority have suffered alteration.</p>
  <p class="product-copy abs" style="left:288px;top:334px">There are many variations of passages of Lorem Ipsum available, but the majority have suffered alteration.</p>
  <p class="product-copy abs" style="left:559px;top:329px">There are many variations of passages of Lorem Ipsum available, but the majority have suffered alteration.</p>
  <span class="btn-more abs" style="left:188px;top:381px">Read more...</span>
  <span class="btn-more abs" style="left:456px;top:381px">Read more...</span>
  <span class="btn-more abs" style="left:725px;top:381px">Read more...</span>
  <div class="shade abs"></div>

  <h2 class="section-title abs" style="left:26px;top:425px">Latest News</h2>
  <div class="news-item abs" style="top:465px"><div class="news-date">15th<br>Jun</div><p class="news-text">Lorem Ipsum is simply dummy text of the printing and typeset-ting industry.</p></div>
  <div class="news-item abs" style="top:531px"><div class="news-date">15th<br>Jun</div><p class="news-text">Lorem Ipsum is simply dummy text of the printing and typeset-ting industry.</p></div>
  <div class="news-item abs" style="top:599px"><div class="news-date">15th<br>Jun</div><p class="news-text">Lorem Ipsum is simply dummy text of the printing and typeset-ting industry.</p></div>

  <h2 class="section-title abs" style="left:290px;top:426px">Quick Contact</h2>
  <span class="form-label abs" style="top:478px">Name</span>
  <span class="form-label abs" style="top:512px">Email</span>
  <span class="form-label abs" style="top:546px">Message</span>
  <div class="field abs" style="top:477px"></div>
  <div class="field abs" style="top:510px"></div>
  <div class="field abs" style="top:544px;height:57px"></div>
  <div class="btn-submit abs">Submit</div>

  <h2 class="section-title abs" style="left:564px;top:425px">Location</h2>
  <div class="map abs" role="img" aria-label="Street map of the office location"></div>
  <p class="contact-info abs" style="top:576px;line-height:13px">Address : 25b, type your address here ,<br><span style="padding-left:52px">new roadds,</span></p>
  <p class="contact-info abs" style="top:613px">Phone : 0240 3817 592</p>
  <p class="contact-info abs" style="top:638px">e-Mail : info@korvant-trading.com</p>
</main>

<nav class="foot-nav abs">
  <a href="#" style="width:92px">Home</a>
  <a href="#" style="width:115px">About Us</a>
  <a href="#" style="width:139px">Functionalities</a>
  <a href="#" style="width:107px">Products</a>
  <a href="#">Contact Us</a>
</nav>
<span class="social abs" style="left:726px;background:#2d5aa8"></span>
<span class="social abs" style="left:760px;background:#47a6d8"></span>
<span class="social abs" style="left:795px;background:#e8741e"></span>

<footer class="site-footer abs">Copyright © 2011. www.korvant-trading.com</footer>
</body>
</html>
```